Moravel Aesthetic Doctor

I require an elegant, luxurious looking business card for my aesthetic business. I am a doctor and that will set me aside from competitors. I am planning to provide home and spa based treatments to clients with high expectations. I have attached my logo.

```html
<!DOCTYPE html>
<html lang="en">
<head>
<meta charset="utf-8">
<title>Moravel Aesthetic Doctor – Business Card</title>
<link rel="stylesheet" href="https://fonts.googleapis.com/css2?family=Marcellus&family=Roboto:wght@300;400&family=Josefin+Sans:wght@400&display=swap">
<style>
  :root {
    --backdrop: #c4c4c4;
    --card: #f3f3f3;
    --card-edge: #e4e4e4;
    --ink: #2b2b2b;
    --brand: #5c6a7a;
    --blue: #3a8fd0;
    --blue-deep: #1766a8;
    --blue-light: #5aaee2;
    --white: #ffffff;
  }
  * { box-sizing: border-box; margin: 0; padding: 0; }
  html, body { width: 1200px; height: 576px; overflow: hidden; }
  body { background: var(--backdrop); position: relative; font-family: "Roboto", sans-serif; color: var(--ink); }

  .card {
    position: absolute; top: 138px; width: 484px; height: 294px;
    border-radius: 10px; overflow: hidden;
    background: linear-gradient(135deg, var(--white) 0%, var(--card) 55%, var(--card-edge) 100%);
    box-shadow: 2px 3px 6px rgba(0,0,0,.25);
  }
  .card--front { left: 81px; }
  .card--back { left: 602px; }

  /* front */
  .brand-lockup { position: absolute; left: 80px; top: 64px; display: flex; align-items: center; gap: 18px; }
  .brand-mark { width: 78px; height: 78px; border: 2px solid var(--brand); border-radius: 50%; flex: none; }
  .brand-name { font-family: "Marcellus", serif; font-weight: 400; color: var(--brand); line-height: 1; }
  .brand-name__main { display: block; font-size: 50px; letter-spacing: 1px; }
  .brand-name__sub { display: block; font-size: 19px; letter-spacing: 1.5px; margin-top: 4px; padding-left: 3px; }

  .services { position: absolute; left: 0; right: 0; top: 196px; text-align: center; font-size: 13px; line-height: 19px; }
  .services .sep { color: var(--blue); margin: 0 7px; }

  .band {
    position: absolute; left: 0; right: 0; top: 240px; height: 34px;
    background: linear-gradient(90deg, var(--blue-deep) 0%, var(--blue) 60%, var(--blue-light) 100%);
    color: var(--white); font-family: "Josefin Sans", sans-serif; font-size: 13px; letter-spacing: 1.2px;
    display: flex; align-items: center; justify-content: center; padding-top: 2px;
  }

  /* back */
  .back-art {
    position: absolute; right: 0; top: 0; width: 270px; height: 100%;
    background: linear-gradient(100deg, rgba(90,174,226,0) 0%, rgba(90,174,226,.55) 30%, var(--blue) 65%, var(--blue-deep) 100%);
  }
  .back-brand { position: absolute; left: 20px; top: 28px; font-family: "Marcellus", serif; color: var(--brand); line-height: 1; }
  .back-brand .brand-name__main { font-size: 44px; }
  .back-brand .brand-name__sub { font-size: 18px; }

  .doctor { position: absolute; left: 20px; top: 140px; }
  .doctor__name { font-size: 18px; font-weight: 300; color: var(--ink); }
  .doctor__post { font-size: 10px; color: var(--blue); margin-left: 3px; }
  .doctor__diploma { font-size: 12.5px; color: var(--blue); line-height: 16px; margin-top: 4px; }

  .contacts { position: absolute; left: 20px; top: 218px; list-style: none; font-size: 12.5px; }
  .contacts li { display: flex; align-items: center; height: 19px; }
  .contacts svg { width: 10px; height: 10px; margin-right: 9px; fill: var(--blue); }
  .contacts .sep { color: var(--blue); margin: 0 6px; }
  .social { display: inline-block; width: 11px; height: 11px; border-radius: 50%; background: var(--blue); margin-left: 4px; }
</style>
</head>
<body>
  <section class="card card--front">
    <div class="brand-lockup">
      <span class="brand-mark"></span>
      <div class="brand-name">
        <span class="brand-name__main">MORAVEL</span>
        <span class="brand-name__sub">AESTHETIC DOCTOR</span>
      </div>
    </div>
    <p class="services">
      Dermal Injectables<span class="sep">|</span>Plasma Facials<span class="sep">|</span>Microneedling<br>
      Skin Boosters<span class="sep">|</span>Excessive Sweating
    </p>
    <div class="band">HOME AND SPA BASED TREATMENTS</div>
  </section>

  <section class="card card--back">
    <div class="back-art" role="img" aria-label="Flowing blue abstract illustration in profile"></div>
    <div class="back-brand">
      <span class="brand-name__main">MORAVEL</span>
      <span class="brand-name__sub">AESTHETIC DOCTOR</span>
    </div>
    <div class="doctor">
      <p><span class="doctor__name">Dr Elise Varden</span><span class="doctor__post">MRCPCH MD</span></p>
      <p class="doctor__diploma">Australasian Diploma of<br>Aesthetic Medicine</p>
    </div>
    <ul class="contacts">
      <li><svg viewBox="0 0 10 10"><path d="M2 0.5 L3.6 2.6 L2.7 3.7 Q3.8 6 6.3 7.3 L7.4 6.4 L9.5 8 L8.6 9.5 Q4.5 9.3 0.5 1.4 Z"/></svg>0800 555 014</li>
      <li><svg viewBox="0 0 10 10"><path d="M0.5 2 H9.5 V8.5 H0.5 Z M0.5 2 L5 5.6 L9.5 2" stroke="#f3f3f3" stroke-width=".8"/></svg>elise@moravel.co.nz</li>
      <li><svg viewBox="0 0 10 10"><circle cx="5" cy="5" r="4.5"/><path d="M0.5 5 H9.5 M5 0.5 Q2.5 5 5 9.5 M5 0.5 Q7.5 5 5 9.5" stroke="#f3f3f3" stroke-width=".7" fill="none"/></svg>www.moravel.co.nz<span class="sep">|</span>Follow us on:<span class="social"></span><span class="social"></span></li>
    </ul>
  </section>
</body>
</html>
```